MirelaStyle e-commerce website design for shopify platform

I currently have a trendy e-commerce clothing store that is primarily based off of the Southern California Style/Trends. I am looking for a redesign of my shopify template as I don't like my current image. I am looking for a sleek clean design that allows more focus on the products. I like neutral backgrounds and easy to use websites. Should be responsive to mobile devices. I would also like to have some ideas for a slide show picture that notifies customers of free shipping if possible. I do also have a theme template that I purchased through Shopify so one could set the theme up for me and edit it to what I need. My website is mirelastyle.com if you would like to look at the type of products I have. I am also looking to do a logo redesign as well- looking for a more stylish logo that would appeal to an approximate age range of 18-40 year old women. I want to be remembered, something to match the web design.

I like teal/turquoise and grey combos but I don't have to have this as the colors.

Target Market(s)

approx. 18-40

Industry/Entity Type

E-Commerce

Number of Pages Required

2 page

Requirements
Must have
• Menu bar, shopify compatible, easy to access/navigate, responsive to mobile devices, easy product upload
Nice to have
• if able ability to resize pictures all to the same size
Should not have
• not be difficult to navigate both on a reg. computer or mobile device

```html
<!DOCTYPE html>
<html lang="en">
<head>
<meta charset="utf-8">
<title>MirelaStyle – Home</title>
<link rel="stylesheet" href="https://fonts.googleapis.com/css2?family=Open+Sans:wght@400;600;700&family=Oswald:wght@400;500&family=Bebas+Neue&family=Libre+Baskerville&display=swap">
<style>
:root{
  --teal:#1797a6;
  --teal-dark:#117d89;
  --page:#ececec;
  --white:#ffffff;
  --ink:#333333;
  --muted:#777777;
  --line:#d6d6d6;
  --dark:#222222;
  --footer:#e2e2e2;
  --hot:#c9302c;
}
*{box-sizing:border-box;margin:0;padding:0}
html,body{width:1200px;height:2667px;overflow:hidden}
body{background:var(--page);font-family:"Open Sans",Arial,sans-serif;color:var(--ink);position:relative}
.abs{position:absolute}
.topline{left:0;top:0;width:1200px;height:5px;background:var(--teal)}
.brand{left:100px;top:38px;font-family:"Oswald",sans-serif;font-weight:500;font-size:46px;color:var(--dark);line-height:1}
.brand-sub{left:178px;top:88px;font-size:11px;color:#d47a8a}
.account-links{left:778px;top:26px;font-size:13px;color:var(--ink)}
.account-links span{margin:0 6px;color:var(--muted)}
.lang{left:1031px;top:18px;width:64px;height:30px;border:1px solid var(--line);background:var(--white);display:flex;align-items:center}
.lang .flag{width:20px;height:13px;margin-left:8px;background:linear-gradient(#b22 0 50%,#fff 50%);border:1px solid #999}
.lang .caret{margin-left:auto;width:22px;height:100%;border-left:1px solid var(--line);display:flex;align-items:center;justify-content:center}
.search{left:892px;top:62px;width:207px;height:36px;border:1px solid var(--line);background:var(--white);display:flex;align-items:center;padding:0 10px;font-size:14px}
.search svg{margin-left:auto}
.nav{left:100px;top:116px;width:999px;height:71px;background:var(--teal);display:flex;align-items:center;box-shadow:0 14px 12px -10px rgba(0,0,0,.25)}
.nav a{color:var(--white);text-decoration:none;font-size:13.5px;font-weight:600;height:100%;display:flex;align-items:center}
.nav a.active{background:var(--dark);width:117px;justify-content:center}
.slider{left:100px;top:220px;width:999px;height:568px;background:var(--white);border:1px solid var(--line);padding:12px;box-shadow:0 2px 4px rgba(0,0,0,.08)}
.slide-img{position:relative;width:100%;height:100%;background:linear-gradient(120deg,#6f7a3c,#b2a57e 45%,#d8cfc2 60%,#8a7a5e)}
.slide-title{position:absolute;right:82px;top:208px;font-family:"Bebas Neue",sans-serif;font-size:62px;color:var(--white);letter-spacing:1px}
.slide-sub{position:absolute;right:84px;top:280px;font-family:"Bebas Neue",sans-serif;font-size:44px;color:var(--dark)}
.arrow{position:absolute;width:52px;height:55px;background:rgba(30,30,30,.85);display:flex;align-items:center;justify-content:center;top:247px}
.dots{position:absolute;left:470px;bottom:12px;display:flex;gap:8px}
.dots i{width:14px;height:14px;border-radius:50%;border:2px solid var(--white);background:transparent}
.dots i.on{background:var(--teal)}
.promo{top:818px;height:181px;background:var(--white);padding:6px;box-shadow:3px 6px 8px rgba(0,0,0,.2)}
.promo-img{width:100%;height:100%;position:relative}
.promo h3{position:absolute;font-family:"Libre Baskerville",serif;font-weight:400;text-align:right;line-height:1.1}
.promo p{position:absolute;font-size:9.5px;font-weight:700;text-align:right;line-height:1.35}
.section-bar{left:100px;top:1049px;width:999px;height:48px;background:var(--white);border:1px solid var(--line)}
.section-tab{position:absolute;left:-1px;top:-1px;height:48px;width:185px;background:var(--teal);color:var(--white);font-size:18px;font-weight:600;display:flex;align-items:center;padding-left:26px;clip-path:polygon(0 0,100% 0,92% 50%,100% 100%,0 100%)}
.bar-nav{position:absolute;right:-1px;top:-1px;display:flex}
.bar-nav span{width:49px;height:48px;background:var(--teal);display:flex;align-items:center;justify-content:center;margin-left:1px}
.product{width:235px;height:358px;background:var(--white);border:1px solid var(--line);padding:5px}
.product-img{width:100%;height:300px;position:relative}
.price{position:absolute;right:0;bottom:0;background:var(--teal);color:var(--white);font-size:15px;width:72px;height:33px;display:flex;align-items:center;justify-content:center}
.product-name{text-align:center;font-size:16px;font-weight:600;margin-top:16px}
.widget{top:1950px;height:230px;background:var(--white);border:1px solid var(--line)}
.widget-head{height:43px;background:var(--teal);color:var(--white);font-size:15px;font-weight:600;display:flex;align-items:center;padding:0 14px}
.about-text{padding:22px 12px;font-size:12.5px;line-height:2;text-align:center}
.tweet{display:flex;gap:10px;padding:14px 16px 10px 16px;font-size:12px;line-height:1.55;border-bottom:1px solid var(--line);margin:0 6px}
.tweet b{color:var(--hot);font-weight:400}
.tweet-meta{font-size:11.5px;margin-top:4px;display:flex;gap:16px;align-items:center}
.follow-btn{margin-left:auto;font-size:10px;background:#eef6fa;color:#333;border:1px solid #bcd;padding:1px 8px;border-radius:3px}
.news-text{padding:18px 14px 12px;font-size:12.5px}
.email{margin:0 14px;height:40px;border:1px solid var(--line);display:flex;align-items:center;padding:0 10px;font-size:12px}
.submit{position:absolute;right:16px;bottom:22px;width:119px;height:42px;background:var(--teal);color:var(--white);font-size:15px;display:flex;align-items:center;justify-content:center}
.feature{top:2226px;height:121px;background:var(--white);border:1px solid var(--line);display:flex;align-items:center;padding-left:20px;gap:14px}
.feature h4{font-family:Arial,sans-serif;font-size:23px;font-weight:700;color:#444}
.feature p{font-size:12.5px;color:var(--muted);margin-top:2px}
.feature p em{font-style:normal;color:var(--teal)}
.footer{left:0;top:2382px;width:1200px;height:219px;background:var(--footer);border-top:4px solid var(--teal)}
.footer h5{font-family:"Oswald",sans-serif;font-weight:400;font-size:16px;color:var(--ink);margin-bottom:14px}
.footer ul{list-style:none;font-size:13px;color:#555}
.footer li{margin-bottom:12px}
.footer li::before{content:"• ";color:#555}
.social li::before{content:none}
.social li{display:flex;align-items:center;gap:10px;margin-bottom:10px}
.social i{width:24px;height:24px;border-radius:50%;background:#666}
.foot-brand{font-family:"Oswald",sans-serif;font-weight:500;font-size:38px;color:var(--dark)}
.foot-text{font-size:12px;color:#555;line-height:1.6;margin-top:8px}
.bottombar{left:0;top:2601px;width:1200px;height:66px;background:var(--dark);color:#eee;font-size:12px;display:flex;align-items:center;padding:0 100px}
.cards{margin-left:auto;display:flex;gap:8px}
.cards i{width:32px;height:21px;border-radius:2px;background:#cfd6e0}
</style>
</head>
<body>
<div class="abs topline"></div>

<header>
  <div class="abs brand">MirelaStyle</div>
  <div class="abs brand-sub">clothing</div>
  <div class="abs account-links">Log in <span>/</span> Create an account <span>/</span> 0 items</div>
  <div class="abs lang"><span class="flag"></span><span class="caret"><svg width="8" height="5"><path d="M0 0h8L4 5z" fill="#888"/></svg></span></div>
  <div class="abs search">Search
    <svg width="20" height="20" viewBox="0 0 20 20"><circle cx="8" cy="8" r="6" fill="none" stroke="#111" stroke-width="2.5"/><path d="M12.5 12.5l6 6" stroke="#111" stroke-width="3"/></svg>
  </div>
  <nav class="abs nav">
    <a class="active" href="#">Home</a>
    <a href="#" style="margin-left:14px">What's New?</a>
    <a href="#" style="margin-left:56px">Dresses</a>
    <a href="#" style="margin-left:56px">Tops</a>
    <a href="#" style="margin-left:56px">Bottoms/Rompers</a>
    <a href="#" style="margin-left:58px">Accessories</a>
    <a href="#" style="margin-left:56px">Sale</a>
    <a href="#" style="margin-left:54px">A little about me</a>
  </nav>
</header>

<section class="abs slider">
  <div class="slide-img" role="img" aria-label="Hero photo: woman in a floral summer dress with a bicycle on a sunlit tree-lined path">
    <div class="slide-title">THE NEW COLLECTIONS</div>
    <div class="slide-sub">Up To 50 %</div>
    <div class="arrow" style="left:0"><svg width="14" height="20"><path d="M11 2L3 10l8 8" stroke="#fff" stroke-width="3" fill="none"/></svg></div>
    <div class="arrow" style="right:0"><svg width="14" height="20"><path d="M3 2l8 8-8 8" stroke="#fff" stroke-width="3" fill="none"/></svg></div>
    <div class="dots"><i class="on"></i><i></i><i></i></div>
  </div>
</section>

<section class="abs promo" style="left:100px;width:487px">
  <div class="promo-img" role="img" aria-label="Promo photo: two women in cream and black outfits on a mauve backdrop" style="background:linear-gradient(90deg,#e8e0e4,#c9b3bf 45%,#8d6a7d)">
    <h3 style="right:10px;top:14px;font-size:23px;color:#fff">SIMPLE<br>INSTALLATION</h3>
    <p style="right:10px;top:76px;width:180px;color:#fff">There are many variations of passages of Lorem Ipsum available, but the majority have suffered alteration in some form</p>
  </div>
</section>
<section class="abs promo" style="left:612px;width:487px">
  <div class="promo-img" role="img" aria-label="Promo photo: woman with flowing hair in a white top against a pale sky" style="background:linear-gradient(90deg,#7e8a7a,#cfd8cc 45%,#e9eee6)">
    <h3 style="right:10px;top:14px;font-size:34px;color:#6aaab0">SOLARA</h3>
    <p style="right:10px;top:56px;width:230px;color:#5a9aa0">There are many variations of passages of Lorem Ipsum available, but the majority have suffered alteration in some form, by injected humour, or randomised words which don't look even slightly believable.</p>
  </div>
</section>

<section class="abs section-bar">
  <div class="section-tab">Whats New!</div>
  <div class="bar-nav">
    <span><svg width="8" height="12"><path d="M6 1L2 6l4 5" stroke="#fff" stroke-width="2" fill="none"/></svg></span>
    <span><svg width="8" height="12"><path d="M2 1l4 5-4 5" stroke="#fff" stroke-width="2" fill="none"/></svg></span>
  </div>
</section>

<!-- Product grid -->
<article class="abs product" style="left:100px;top:1129px"><div class="product-img" role="img" aria-label="Product photo: black strapless playsuit" style="background:linear-gradient(#eceae8,#d9cfc6)"><span class="price">$42.00</span></div><div class="product-name">Cora Playsuit</div></article>
<article class="abs product" style="left:354px;top:1129px"><div class="product-img" role="img" aria-label="Product photo: cream lace flared trousers" style="background:linear-gradient(#d8c7bd,#efe6dc)"><span class="price">$42.00</span></div><div class="product-name">Cora Playsuit</div></article>
<article class="abs product" style="left:608px;top:1129px"><div class="product-img" role="img" aria-label="Product photo: blue printed flared trousers" style="background:linear-gradient(#e6e6e8,#4a6c8c)"><span class="price">$42.00</span></div><div class="product-name">Cora Playsuit</div></article>
<article class="abs product" style="left:864px;top:1129px"><div class="product-img" role="img" aria-label="Product photo: white bell-sleeve tunic dress" style="background:linear-gradient(#6b7a5a,#e8e4de 60%)"><span class="price">$42.00</span></div><div class="product-name">Cora Playsuit</div></article>

<article class="abs product" style="left:100px;top:1532px"><div class="product-img" role="img" aria-label="Product photo: pink patterned flared trousers" style="background:linear-gradient(#d6d8de,#b08a86)"><span class="price">$42.00</span></div><div class="product-name">Cora Playsuit</div></article>
<article class="abs product" style="left:354px;top:1532px"><div class="product-img" role="img" aria-label="Product photo: floral blazer on a hanger" style="background:linear-gradient(#c9c9c9,#d8b8c0)"><span class="price">$42.00</span></div><div class="product-name">Cora Playsuit</div></article>
<article class="abs product" style="left:608px;top:1532px"><div class="product-img" role="img" aria-label="Product photo: turquoise floral mini dress" style="background:linear-gradient(#e4e2df,#9fd0cc)"><span class="price">$42.00</span></div><div class="product-name">Cora Playsuit</div></article>
<article class="abs product" style="left:864px;top:1532px"><div class="product-img" role="img" aria-label="Product photo: black and white tie-dye maxi dress" style="background:linear-gradient(#d9d9d9,#4d5358)"><span class="price">$42.00</span></div><div class="product-name">Cora Playsuit</div></article>

<section class="abs widget" style="left:100px;width:318px">
  <div class="widget-head">Little About us</div>
  <p class="about-text">My name is Jinelle (pronounced Janelle with a "J") and I have always loved fashion! In 2004, I moved to LA to pursue my love. I have finally made it a reality by opening my own boutique. We currently carry a variety of different labels and hope to incorporate our own in the near future!</p>
</section>

<section class="abs widget" style="left:443px;width:316px">
  <div class="widget-head">Latest Tweets <span class="follow-btn">Follow</span></div>
  <div class="tweet"><svg width="12" height="12" style="flex:none;margin-top:3px"><rect width="12" height="12" fill="#222"/></svg><div><b>Chirper Name:</b> The connection to chirper has returned an error. Please try again later.<div class="tweet-meta"><span>◷ about 15 hours ago</span><span>◉ Open tweet</span></div></div></div>
  <div class="tweet" style="border:0"><svg width="12" height="12" style="flex:none;margin-top:3px"><rect width="12" height="12" fill="#222"/></svg><div><b>Chirper Name:</b> The connection to chirper has returned an error. Please try again later.<div class="tweet-meta"><span>◷ about 15 hours ago</span><span>◉ Open tweet</span></div></div></div>
</section>

<section class="abs widget" style="left:782px;width:317px">
  <div class="widget-head">Newsletters</div>
  <p class="news-text">We promise to only send you good things.</p>
  <div class="email">Email Address
    <svg width="20" height="14" style="margin-left:auto"><rect width="20" height="14" fill="#999"/><path d="M0 0l10 8 10-8" stroke="#fff" stroke-width="1.5" fill="none"/></svg>
  </div>
  <div class="submit">Submit</div>
</section>

<section class="abs feature" style="left:100px;width:328px">
  <div role="img" aria-label="Illustration: green delivery truck" style="width:100px;height:70px;background:linear-gradient(#5cb85c,#3f8f3f);border-radius:6px"></div>
  <div><h4>FREE SHIPPING !</h4><p>Free shipping on orders over $100</p></div>
</section>
<section class="abs feature" style="left:436px;width:328px">
  <svg width="86" height="86" role="img" aria-label="Guarantee badge"><circle cx="43" cy="43" r="41" fill="#c9a227"/></svg>
  <div><h4>MONEY BACK !</h4><p>Money Back Guarantee 30 days</p></div>
</section>
<section class="abs feature" style="left:772px;width:327px;align-items:flex-start;padding-top:0">
  <svg width="40" height="92" role="img" aria-label="Hot offer ribbon"><path d="M0 0h40v92l-20-14L0 92z" fill="var(--hot)"/></svg>
  <div style="margin-top:38px"><h4>BUY 1 GET 1</h4><p>Start: Jun <em>23</em> 2013 - End: Jul <em>25</em> 2013</p></div>
</section>

<footer class="abs footer">
  <div class="abs" style="left:100px;top:30px;width:220px">
    <div class="foot-brand">MirelaStyle</div>
    <p class="foot-text">Lorem Ipsum is simply dummy text the printing and typesetting industry.</p>
  </div>
  <div class="abs" style="left:391px;top:30px">
    <h5>THE SERVICE</h5>
    <ul><li>My Account</li><li>Order History</li><li>Wish List</li><li>Returns</li><li>Site Map</li></ul>
  </div>
  <div class="abs" style="left:661px;top:30px">
    <h5>FOLLOW US</h5>
    <ul class="social"><li><i></i>Facepage</li><li><i></i>Chirper</li><li><i></i>RSS</li><li><i></i>Snapgrid</li></ul>
  </div>
  <div class="abs" style="left:935px;top:30px">
    <h5>INFOMATION</h5>
    <ul><li>About us</li><li>Delivery Information</li><li>Privacy Policy</li><li>Terms &amp; Condition</li><li>Contact Us</li></ul>
  </div>
</footer>

<div class="abs bottombar">Copyright 2014 MirelaStyle All Rights Reserved.
  <div class="cards"><i></i><i></i><i></i><i></i><i></i></div>
</div>
</body>
</html>
```